Packaging design for a reclosable bag for our product

We have a logo, and we need to put it on packaging for our product and while we want the look to be simple, we want it to follow good design principles and also contain spaces for other product descriptions.

There will be 5 sizes at launch so I'd like 5 variations, one for each size.

I've included a few mockups of the type of bag that I made but they are all just rough ideas that I had.

I want the brand to look scientific and methodical and even a bit quirky, as in "wow this is a serious product but also a bit unusual."

```html
<!DOCTYPE html>
<html lang="en">
<head>
<meta charset="utf-8">
<title>Lumera Bias Lighting – Pouch Range</title>
<link href="https://fonts.googleapis.com/css2?family=Nunito:wght@400;800&display=swap" rel="stylesheet">
<style>
  :root {
    --page-bg: #ffffff;
    --pouch: #1d1d1d;
    --pouch-edge: #161616;
    --band: #2c2c2c;
    --band-dark: #151515;
    --seam: #0e0e0e;
    --ink: #ffffff;
    --size-xs: #e3151c;
    --size-s: #6cb51f;
    --size-m: #f2c200;
    --size-l: #ef7510;
    --size-xl: #0a8fe3;
    --size-xxl: #8e3bc0;
  }
  * { box-sizing: border-box; margin: 0; padding: 0; }
  html, body {
    width: 1200px; height: 800px; overflow: hidden;
    background: var(--page-bg);
    font-family: "Nunito", sans-serif;
  }
  .range {
    width: 1200px; height: 800px;
    display: grid;
    grid-template-columns: repeat(3, 330px);
    grid-template-rows: repeat(2, 360px);
    gap: 30px 40px;
    justify-content: center;
    align-content: center;
  }
  .pouch {
    position: relative;
    background: var(--pouch);
    border-radius: 16px 16px 3px 3px;
    overflow: hidden;
    color: var(--ink);
  }
  .pouch__band {
    position: absolute; top: 0; bottom: 0; left: 0;
    width: 54px;
    background: var(--band);
  }
  .pouch__zip {
    position: absolute; left: 0; right: 0; height: 3px;
    background: var(--seam);
  }
  .pouch__zip--upper { top: 40px; }
  .pouch__zip--lower { top: 52px; height: 2px; }
  .pouch__zip--seal { top: 68px; height: 4px; }
  .pouch__notch {
    position: absolute; top: 30px; width: 5px; height: 6px;
    background: var(--page-bg);
  }
  .pouch__notch--left { left: 0; clip-path: polygon(0 0, 100% 50%, 0 100%); }
  .pouch__notch--right { right: 0; clip-path: polygon(100% 0, 0 50%, 100% 100%); }
  .size-tab {
    position: absolute; left: 0; top: 204px;
    width: 54px; height: 70px;
    background: var(--band-dark);
  }
  .size-tab__label {
    position: absolute; left: 2px; top: 10px;
    width: 52px; height: 50px;
    background: var(--accent);
    display: flex; align-items: center; justify-content: center;
    font-weight: 800; font-size: 22px; letter-spacing: 0.5px;
  }
  .size-tab__label--wide { font-size: 19px; }
  .label {
    position: absolute; left: 68px; top: 160px; right: 8px;
  }
  .label__brand {
    font-weight: 800; font-size: 38px; line-height: 1;
    letter-spacing: -1px;
  }
  .label__product {
    margin-top: 8px;
    font-weight: 800; font-size: 21px; line-height: 1.1;
  }
  .label__length {
    margin-top: 8px;
    font-size: 13px; color: var(--accent);
  }
  .label__spec {
    margin-top: 10px;
    font-size: 13px; line-height: 1.45;
  }
  .pouch--xs { --accent: var(--size-xs); }
  .pouch--s { --accent: var(--size-s); }
  .pouch--m { --accent: var(--size-m); }
  .pouch--l { --accent: var(--size-l); }
  .pouch--xl { --accent: var(--size-xl); }
  .pouch--xxl { --accent: var(--size-xxl); }
</style>
</head>
<body>
<main class="range">

  <article class="pouch pouch--xs">
    <div class="pouch__band"></div>
    <div class="pouch__zip pouch__zip--upper"></div>
    <div class="pouch__zip pouch__zip--lower"></div>
    <div class="pouch__zip pouch__zip--seal"></div>
    <span class="pouch__notch pouch__notch--left"></span>
    <span class="pouch__notch pouch__notch--right"></span>
    <div class="size-tab"><span class="size-tab__label">XS</span></div>
    <div class="label">
      <p class="label__brand">Lumera</p>
      <p class="label__product">Bias Lighting</p>
      <p class="label__length">1 Meter / 3.3 Feet</p>
      <p class="label__spec">White Bias Lighting<br>6500K / Simulated D65 / CRI 90+</p>
    </div>
  </article>

  <article class="pouch pouch--s">
    <div class="pouch__band"></div>
    <div class="pouch__zip pouch__zip--upper"></div>
    <div class="pouch__zip pouch__zip--lower"></div>
    <div class="pouch__zip pouch__zip--seal"></div>
    <span class="pouch__notch pouch__notch--left"></span>
    <span class="pouch__notch pouch__notch--right"></span>
    <div class="size-tab"><span class="size-tab__label">S</span></div>
    <div class="label">
      <p class="label__brand">Lumera</p>
      <p class="label__product">Bias Lighting</p>
      <p class="label__length">2 Meters / 6.6 Feet</p>
      <p class="label__spec">White Bias Lighting<br>6500K / Simulated D65 / CRI 90+</p>
    </div>
  </article>

  <article class="pouch pouch--m">
    <div class="pouch__band"></div>
    <div class="pouch__zip pouch__zip--upper"></div>
    <div class="pouch__zip pouch__zip--lower"></div>
    <div class="pouch__zip pouch__zip--seal"></div>
    <span class="pouch__notch pouch__notch--left"></span>
    <span class="pouch__notch pouch__notch--right"></span>
    <div class="size-tab"><span class="size-tab__label">M</span></div>
    <div class="label">
      <p class="label__brand">Lumera</p>
      <p class="label__product">Bias Lighting</p>
      <p class="label__length">3 Meters / 9.8 Feet</p>
      <p class="label__spec">White Bias Lighting<br>6500K / Simulated D65 / CRI 90+</p>
    </div>
  </article>

  <article class="pouch pouch--l">
    <div class="pouch__band"></div>
    <div class="pouch__zip pouch__zip--upper"></div>
    <div class="pouch__zip pouch__zip--lower"></div>
    <div class="pouch__zip pouch__zip--seal"></div>
    <span class="pouch__notch pouch__notch--left"></span>
    <span class="pouch__notch pouch__notch--right"></span>
    <div class="size-tab"><span class="size-tab__label">L</span></div>
    <div class="label">
      <p class="label__brand">Lumera</p>
      <p class="label__product">Bias Lighting</p>
      <p class="label__length">4 Meters / 13.1 Feet</p>
      <p class="label__spec">White Bias Lighting<br>6500K / Simulated D65 / CRI 90+</p>
    </div>
  </article>

  <article class="pouch pouch--xl">
    <div class="pouch__band"></div>
    <div class="pouch__zip pouch__zip--upper"></div>
    <div class="pouch__zip pouch__zip--lower"></div>
    <div class="pouch__zip pouch__zip--seal"></div>
    <span class="pouch__notch pouch__notch--left"></span>
    <span class="pouch__notch pouch__notch--right"></span>
    <div class="size-tab"><span class="size-tab__label">XL</span></div>
    <div class="label">
      <p class="label__brand">Lumera</p>
      <p class="label__product">Bias Lighting</p>
      <p class="label__length">5 Meters / 16.4 Feet</p>
      <p class="label__spec">White Bias Lighting<br>6500K / Simulated D65 / CRI 90+</p>
    </div>
  </article>

  <article class="pouch pouch--xxl">
    <div class="pouch__band"></div>
    <div class="pouch__zip pouch__zip--upper"></div>
    <div class="pouch__zip pouch__zip--lower"></div>
    <div class="pouch__zip pouch__zip--seal"></div>
    <span class="pouch__notch pouch__notch--left"></span>
    <span class="pouch__notch pouch__notch--right"></span>
    <div class="size-tab"><span class="size-tab__label size-tab__label--wide">XXL</span></div>
    <div class="label">
      <p class="label__brand">Lumera</p>
      <p class="label__product">Bias Lighting</p>
      <p class="label__length">6 Meters / 19.7 Feet</p>
      <p class="label__spec">White Bias Lighting<br>6500K / Simulated D65 / CRI 90+</p>
    </div>
  </article>

</main>
</body>
</html>
```